Business Card Design Project

Doctor, Pain Management. Need a new business card design with appointment info on the back. New address is 18 Corvell Road, Suite 304, Brisdale, NJ 07391. Right now I believe the rest of the information is staying the same.

```html
<!DOCTYPE html>
<html lang="en">
<head>
<meta charset="utf-8">
<title>Steadfast Pain Care – Business Card</title>
<link href="https://fonts.googleapis.com/css2?family=Open+Sans:wght@400;600;700&family=Arimo:wght@400&display=swap" rel="stylesheet">
<style>
  :root {
    --bg: #e9e6e1;
    --charcoal: #2b2b2b;
    --panel-grey: #ecebeb;
    --orange: #e8590c;
    --ink: #2e2e2e;
    --text-grey: #4a4a4a;
    --white: #ffffff;
  }
  * { box-sizing: border-box; margin: 0; padding: 0; }
  html, body {
    width: 1200px; height: 900px; overflow: hidden;
    background: var(--bg);
    font-family: "Open Sans", Arial, sans-serif;
  }
  .stage {
    position: relative; width: 1200px; height: 900px;
    display: flex; flex-direction: column; align-items: center; justify-content: center; gap: 56px;
  }
  .card {
    position: relative; width: 620px; height: 354px; overflow: hidden;
    box-shadow: 0 6px 18px rgba(0,0,0,0.18);
  }

  /* ---------- Back: appointment side ---------- */
  .card-back { background: var(--charcoal); }
  .appt-header {
    height: 84px; display: flex; align-items: center; justify-content: center;
    color: var(--white); font-size: 23px; font-weight: 600; letter-spacing: 0.2px;
  }
  .appt-form {
    background: var(--panel-grey); height: 186px; padding: 38px 38px 0 38px;
    color: var(--text-grey); font-size: 16px;
  }
  .form-row { display: flex; align-items: flex-end; gap: 14px; margin-bottom: 20px; }
  .field { display: flex; align-items: flex-end; gap: 6px; white-space: nowrap; }
  .field-label { flex: none; white-space: nowrap; }
  .field-line { border-bottom: 2px dotted #6a6a6a; height: 16px; flex: none; }
  .days { display: flex; gap: 18px; margin-top: 4px; flex-wrap: nowrap; }
  .day { display: flex; align-items: center; gap: 6px; font-size: 15px; white-space: nowrap; }
  .checkbox {
    width: 20px; height: 20px; border: 2px solid #8a8a8a; background: var(--white);
  }
  .appt-footer {
    height: 84px; display: flex; align-items: center; justify-content: center;
    color: #cfcfcf; font-size: 14px;
  }

  /* ---------- Front: contact side ---------- */
  .card-front { background: var(--white); }
  .front-art { position: absolute; inset: 0; }
  .doctor { position: absolute; left: 36px; top: 40px; }
  .doctor-name {
    color: var(--orange); font-weight: 700; font-size: 20px; letter-spacing: 0.3px; white-space: nowrap;
  }
  .doctor-title { color: var(--ink); font-size: 15px; margin-top: 2px; }
  .practice {
    position: absolute; right: 34px; top: 100px;
    display: flex; align-items: center; gap: 10px;
  }
  .practice-dot { width: 16px; height: 16px; border-radius: 50%; background: var(--orange); }
  .practice-name {
    font-family: "Arimo", Arial, sans-serif; font-size: 22px; color: var(--ink); white-space: nowrap;
  }
  .contact {
    position: absolute; left: 38px; top: 178px; list-style: none;
    color: var(--ink); font-size: 16px; line-height: 23px;
  }
  .contact li { display: flex; align-items: center; gap: 7px; white-space: nowrap; }
  .contact svg { width: 14px; height: 14px; fill: var(--orange); flex: none; }
  .address {
    position: absolute; right: 30px; top: 262px; text-align: right; font-style: normal;
    color: var(--white); font-size: 14px; line-height: 21px; white-space: nowrap;
  }
</style>
</head>
<body>
<main class="stage">

  <section class="card card-back" aria-label="Appointment card, back side">
    <div class="appt-header">Your Next Appointment on</div>
    <div class="appt-form">
      <div class="form-row">
        <div class="field"><span class="field-label">Name :</span><span class="field-line" style="width:190px"></span></div>
        <div class="field"><span class="field-label">Time :</span><span class="field-line" style="width:120px"></span><span class="field-label">AM / PM</span></div>
      </div>
      <div class="form-row">
        <div class="field"><span class="field-label">Date :</span><span class="field-line" style="width:196px"></span></div>
      </div>
      <div class="days">
        <span class="day"><span class="checkbox"></span>MON</span>
        <span class="day"><span class="checkbox"></span>TUE</span>
        <span class="day"><span class="checkbox"></span>WED</span>
        <span class="day"><span class="checkbox"></span>THU</span>
        <span class="day"><span class="checkbox"></span>FRI</span>
        <span class="day"><span class="checkbox"></span>SAT</span>
      </div>
    </div>
    <div class="appt-footer">If unable to keep your appointment, please contact us as soon as possible</div>
  </section>

  <section class="card card-front" aria-label="Business card, front side">
    <svg class="front-art" viewBox="0 0 620 354" aria-hidden="true">
      <path d="M0 340 C 200 332, 380 300, 470 232 C 530 182, 570 150, 620 145 L620 354 L0 354 Z" fill="#2b2b2b"/>
      <path d="M0 318 C 180 316, 360 292, 472 228 C 380 298, 200 330, 0 340 Z" fill="#e8590c"/>
      <path d="M0 314 C 180 312, 360 288, 474 224" fill="none" stroke="#ffffff" stroke-width="3"/>
    </svg>

    <div class="doctor">
      <div class="doctor-name">DR. LIANMEI ZHOU, M.D., PH.D.</div>
      <div class="doctor-title">Board Certified Anesthesiologist</div>
    </div>

    <div class="practice">
      <span class="practice-dot"></span>
      <span class="practice-name">Steadfast Pain Care</span>
    </div>

    <ul class="contact">
      <li><svg viewBox="0 0 16 16"><path d="M3 1l3 3-1.5 2a9 9 0 0 0 5.5 5.5L12 10l3 3-2 2C7 15 1 9 1 3z"/></svg>973.555.0148</li>
      <li><svg viewBox="0 0 16 16"><path d="M4 1h8v4H4zM1 6h14v6h-3v3H4v-3H1zM5 10v4h6v-4z"/></svg>973.555.0162</li>
      <li><svg viewBox="0 0 16 16"><circle cx="8" cy="8" r="7"/></svg>www.steadfastpaincare.com</li>
      <li><svg viewBox="0 0 16 16"><path d="M1 3h14v10H1z M1 3l7 6 7-6" stroke="#fff" stroke-width="1.2"/></svg>steadfastpc.office@mailbox.com</li>
    </ul>

    <address class="address">
      18 Corvell Road, Suite 304<br>Brisdale, NJ 07391
    </address>
  </section>

</main>
</body>
</html>
```